Storm Restoration Contractor needs a professional letterhead design

Looking for a professional letterhead design. Not looking for your cheapo MS Word standard ones that are readily available. Dont want it to be cookie cutter look like ones readily available online. We just recently changed our logo and want to freshen up all our documents. Our company handles restoring a property back to a pre-loss condition after a storm damages it. For example, wind, hail, flood, fire losses.

Target Market(s)

Property Owners, Homeowners, Property Owners, Commercial Property Owners, Property Management Companies

Industry/Entity Type

Construction Company

Requirements
Must have
• Professional, Use 1 of 2 logo options
• Storm Restoration, Roofing, Siding, Windows

```html
<!DOCTYPE html>
<html lang="en">
<head>
<meta charset="utf-8">
<title>Stormline Restoration Letterhead</title>
<link href="https://fonts.googleapis.com/css2?family=Arimo:wght@400;700&display=swap" rel="stylesheet">
<style>
  :root {
    --backdrop: #e9e9ea;
    --paper: #ffffff;
    --brand-blue: #1f76c8;
    --brand-grey: #4a4a4c;
    --ink: #2b2b2b;
    --muted-ink: #4d4d4d;
    --on-blue: #ffffff;
  }
  * { box-sizing: border-box; margin: 0; padding: 0; }
  html, body { width: 1200px; height: 795px; overflow: hidden; }
  body {
    background: var(--backdrop);
    font-family: "Arimo", Arial, sans-serif;
    display: flex;
    align-items: center;
    justify-content: center;
  }
  .letterhead {
    position: relative;
    width: 540px;
    height: 764px;
    background: var(--paper);
    box-shadow: 0 2px 10px rgba(0,0,0,0.12);
    overflow: hidden;
  }
  .brand {
    position: absolute;
    top: 58px;
    left: 48px;
  }
  .brand-name {
    font-family: "Arimo", Arial, sans-serif;
    font-weight: 700;
    font-size: 17px;
    color: var(--brand-blue);
  }
  .letter-body {
    position: absolute;
    top: 170px;
    left: 48px;
    width: 430px;
    color: var(--muted-ink);
    font-size: 10.5px;
    line-height: 1.42;
  }
  .salutation {
    font-weight: 700;
    font-size: 13px;
    color: var(--ink);
    margin-bottom: 10px;
  }
  .letter-body p { margin-bottom: 14px; }
  .signature {
    width: 120px;
    height: 40px;
    margin-top: 22px;
    background: linear-gradient(90deg, #f1f1f1, #e2e2e2);
    border-radius: 3px;
  }
  .footer-wave {
    position: absolute;
    left: 0;
    bottom: 0;
    width: 540px;
    height: 764px;
  }
  .contact-list {
    position: absolute;
    right: 22px;
    bottom: 44px;
    list-style: none;
    text-align: right;
    color: var(--on-blue);
    font-size: 10px;
    line-height: 1.75;
  }
  .contact-list li {
    display: flex;
    justify-content: flex-end;
    align-items: center;
    gap: 6px;
  }
  .contact-icon { width: 9px; height: 9px; flex: none; }
</style>
</head>
<body>
  <main class="letterhead">
    <header class="brand">
      <span class="brand-name">Stormline Restoration</span>
    </header>

    <section class="letter-body">
      <p class="salutation">Dear Mr. Carter,</p>
      <p>Lorem Ipsum is simply dummy text of the printing and typesetting industry. Lorem Ipsum has been the industry's standard dummy text ever since the 1500s, when an unknown printer took a galley of type and scrambled it to make a type specimen book. It has survived not only five centuries, but also the leap into electronic typesetting, remaining essentially unchanged.</p>
      <p>The standard chunk of Lorem Ipsum used since the 1500s is reproduced below for those interested. Sections 1.10.32 and 1.10.33 from "de Finibus Bonorum et Malorum" by Cicero are also reproduced in their exact original form, accompanied by English versions from the 1914 translation by H. Rackham.</p>
      <p>Lorem Ipsum is simply dummy text of the printing and typesetting industry. Lorem Ipsum has been the industry's standard dummy text ever since the 1500s, when an unknown printer took a galley of type and scrambled it to make a type specimen book. It has survived not only five centuries, but also the leap into electronic typesetting, remaining essentially unchanged. It was popularised in the</p>
      <div class="signature" role="img" aria-label="Handwritten signature of the sender"></div>
    </section>

    <svg class="footer-wave" viewBox="0 0 540 764" aria-hidden="true">
      <path d="M0,740 C210,728 380,610 540,372" fill="none" stroke="var(--brand-blue)" stroke-width="1.5"/>
      <path d="M0,746 C215,734 385,616 540,388 L540,420 C390,640 215,744 0,752 Z" fill="var(--brand-grey)"/>
      <path d="M0,754 C220,748 392,648 540,432 L540,764 L0,764 Z" fill="var(--brand-blue)"/>
    </svg>

    <ul class="contact-list">
      <li>(555) 214-7730
        <svg class="contact-icon" viewBox="0 0 10 10"><path d="M2 1 L4 1 L4.6 3 L3.5 4 Q4.5 5.8 6 6.5 L7 5.4 L9 6 L9 8 Q5 9 2 5 Q1 3 2 1Z" fill="var(--on-blue)"/></svg></li>
      <li>(555) 214-7731
        <svg class="contact-icon" viewBox="0 0 10 10"><rect x="1" y="3" width="8" height="5" rx="1" fill="var(--on-blue)"/><rect x="3" y="1" width="4" height="2" fill="var(--on-blue)"/></svg></li>
      <li>info@stormlinerestoration.com
        <svg class="contact-icon" viewBox="0 0 10 10"><rect x="1" y="2" width="8" height="6" fill="none" stroke="var(--on-blue)"/><path d="M1 2 L5 5.5 L9 2" fill="none" stroke="var(--on-blue)"/></svg></li>
      <li>www.stormlinerestoration.com
        <svg class="contact-icon" viewBox="0 0 10 10"><circle cx="5" cy="5" r="4" fill="none" stroke="var(--on-blue)"/><path d="M1 5 H9 M5 1 V9" stroke="var(--on-blue)"/></svg></li>
      <li>2280 Harbor Loop, Fairview, CA 95000
        <svg class="contact-icon" viewBox="0 0 10 10"><path d="M5 9.5 C2 6 2 4.5 2 4 A3 3 0 0 1 8 4 C8 4.5 8 6 5 9.5Z" fill="var(--on-blue)"/></svg></li>
    </ul>
  </main>
</body>
</html>
```